Bluefern Business Services needs a new interactive and interesting website

We need an interesting, professional, modern and functional company website for Bluefern Business Services - a young IT Services company based out of Chennai, India.

Bluefern Business Services is a fully owned subsidiary of Marlow Goods, one of the world's leading direct to consumer wine merchant.

We already have a registered company logo which must feature in the website.

We conceive, design, develop, test, implement and support IT solutions across the entire Marlow Goods IT landscape. For ex : We currently run about 25 e-commerce websites for Marlow Goods on ATG and Dot Net.

We would like to see our corporate colors used in the website. (Burgundy wine and wine green - source: www.bluefernbs-site.com)

We are looking at this website to communicate a fun, friendly and professionally managed company - reaching out to career seekers, prospective customers and general public.

For reference - The company name 'Bluefern' is an inspiration from the Marlow Goods lineage.

The second image with the world map is stickered on our main entrance to the office, I am not sure where this can be used -just putting it out there..

Please note that there are only a few more days to submit designs for this contest  !

I would appreciate if you can help posting your designs in time for our review and consideration.

Thanks.

Reason: Thanks for your inputs. We have a number of designers and a lot to digest and work with in the past few days. There has been a rush of new designs in the last few days Hence we will require more time to process these and make our decision. Hence i am requesting the contest to be open for more days. Regards, Tarun

Target Market(s)

Prospective job seekers who want to know more about the company and also wish to apply for a job vacancy
People wanting to know more about the company in general and our progress
People who want to see what we offer and how we can help them too - prospective customers
Companies that are interested in our IT Captive journey and are looking for a business opportunity

Industry/Entity Type

E-Commerce

Requirements
Must have
• Log In/ Register facility acting as a Single Sign on for Intranet (Employees)

Facility to post job vacancies (with an expiry date) and enable people to apply for a role and upload their CV/Resume.

Facility to Review Job applications

Facility for website visitors to contact Bluefern business Services via an online 'Contact Us' form with a split of job seekers and business opportunities

Gallery facility to upload pictures regarding company events
Nice to have
• Less Cluttered and contemporary design
Some Wine/Vineyard inspirations will be good but not too much, the company is an IT services company

```html
<!DOCTYPE html>
<html lang="en">
<head>
<meta charset="utf-8">
<title>Bluefern Business Services</title>
<link href="https://fonts.googleapis.com/css2?family=Open+Sans:wght@300;400;600&family=Ubuntu:wght@400;700&display=swap" rel="stylesheet">
<style>
:root{
  --burgundy:#8a0043;
  --dark:#2b2b2b;
  --olive:#7c8a2e;
  --olive-dark:#66731f;
  --text:#444;
  --muted:#8a8a8a;
  --rule:#dcdcdc;
  --white:#fff;
}
*{margin:0;padding:0;box-sizing:border-box}
html,body{width:1200px;height:1200px;overflow:hidden;background:var(--white);font-family:"Open Sans",Arial,sans-serif;color:var(--text)}
.page{position:relative;width:1200px;height:1200px}
.abs{position:absolute}

.site-header{left:110px;top:0;width:980px;height:112px;background:var(--dark)}
.brand{left:12px;top:14px;display:flex;align-items:center;gap:10px}
.brand-dot{width:38px;height:38px;border-radius:50%;background:var(--white)}
.brand-name{font-family:"Ubuntu",sans-serif;color:var(--white);line-height:1}
.brand-name b{display:block;font-size:46px;font-weight:700}
.brand-name span{display:block;font-size:30px;font-weight:400;margin-top:2px}
.social{right:12px;top:20px;display:flex;gap:30px}
.social i{display:block;width:20px;height:20px;border-radius:50%;background:#6f6f6f}
.search{left:712px;top:59px;width:256px;height:34px;background:var(--white);font-size:12px;color:#aaa;padding:9px 9px}
.search svg{position:absolute;right:8px;top:8px}

.sidebar{left:110px;top:122px;width:300px;height:1021px;background:var(--burgundy);color:var(--white)}
.menu{list-style:none;padding-top:5px}
.menu li{height:35px;display:flex;align-items:center;padding:0 14px;font-size:14.5px;letter-spacing:-0.2px;border-bottom:1px solid rgba(255,255,255,.08);position:relative}
.menu li svg{margin-right:6px}
.menu li .plus{position:absolute;right:14px;top:5px;font-size:18px}
.side-title{font-size:14.5px;left:17px}
.side-text{left:14px;top:315px;width:280px;font-size:12px;line-height:18px;letter-spacing:-0.4px;white-space:nowrap}
.side-work{left:15px;top:485px;width:273px;height:166px;background:linear-gradient(135deg,#f2f4f6,#cdd3d8)}

.hero{left:423px;top:122px;width:667px;height:375px;background:linear-gradient(160deg,#e9edf1 0%,#c9ccd0 45%,#6d6f73 100%)}
.hero-title{left:0;top:224px;height:34px;padding:0 10px;background:var(--burgundy);color:var(--white);font-size:21px;font-weight:600;line-height:34px;letter-spacing:-0.3px}
.hero-sub{left:0;top:258px;width:460px;height:33px;background:rgba(30,30,30,.75);color:var(--white);font-size:12.6px;line-height:33px;padding-left:9px;letter-spacing:-0.2px}
.dots{left:0;top:363px;display:flex;gap:1px}
.dots i{display:block;width:12px;height:12px;background:var(--olive)}
.dots i:nth-child(2){background:#bbb}

.feature{top:512px;width:200px}
.feature h3{font-size:14px;font-weight:400;color:#333;display:flex;align-items:center;gap:6px;height:20px;letter-spacing:-0.2px}
.feature p{margin-top:17px;font-size:12.3px;line-height:18px;color:var(--muted);letter-spacing:-0.3px}
.more{display:inline-block;margin-top:7px;font-size:11px;color:var(--olive-dark);text-decoration:underline;letter-spacing:-0.2px}

.sec-title{font-size:14px;color:#333;letter-spacing:-0.2px}
.rule{height:1px;background:var(--rule)}
.work{top:695px;width:197px}
.work .ph{height:126px}
.work p{margin-top:7px;font-size:12.3px;line-height:18px;color:var(--muted);padding-bottom:11px;border-bottom:1px solid var(--rule);letter-spacing:-0.3px}

.post{left:423px;width:300px;height:60px}
.post .ico{position:absolute;left:0;top:0;width:42px;height:42px;background:var(--burgundy);display:flex;align-items:center;justify-content:center}
.post p{position:absolute;left:53px;top:-2px;width:250px;font-size:12px;line-height:18px;color:var(--muted);letter-spacing:-0.35px;white-space:nowrap}
.post .meta{position:absolute;left:53px;top:40px;font-size:9.5px;color:#999;display:flex;gap:18px}
.post .meta span{display:flex;align-items:center;gap:4px}

.btn{background:linear-gradient(#95a43e,var(--olive-dark));color:var(--white);font-size:14px;font-weight:600;text-align:center;border-radius:2px}
.thumb{width:92px;height:62px}

.site-footer{left:110px;top:1158px;width:980px;height:42px;background:var(--dark);color:#eee;font-size:12.5px;text-align:center;line-height:42px}
</style>
</head>
<body>
<div class="page">

  <header class="site-header abs">
    <div class="brand abs"><div class="brand-dot"></div><div class="brand-name"><b>bluefern</b><span>Business Services</span></div></div>
    <div class="social abs"><i></i><i></i><i></i><i></i><i></i><i></i></div>
    <div class="search abs">Search here....
      <svg width="20" height="20" viewBox="0 0 20 20"><circle cx="8" cy="8" r="6" fill="none" stroke="#ccc" stroke-width="2"/><line x1="12.5" y1="12.5" x2="18" y2="18" stroke="#ccc" stroke-width="2.5"/></svg>
    </div>
  </header>

  <aside class="sidebar abs">
    <ul class="menu">
      <li><svg width="12" height="11"><path d="M6 0 12 6H10V11H2V6H0Z" fill="#fff"/></svg>HOME</li>
      <li><svg width="12" height="11"><rect x="1" y="1" width="10" height="9" fill="#fff"/></svg>ABOUT US<span class="plus">+</span></li>
      <li><svg width="13" height="11"><rect x="0" y="1" width="13" height="9" fill="#fff"/><circle cx="6.5" cy="5.5" r="2.5" fill="#8a0043"/></svg>CLIENTS<span class="plus">+</span></li>
      <li><svg width="13" height="11"><path d="M0 1H3L4 7H11L12 3H4" fill="none" stroke="#fff" stroke-width="2"/><circle cx="5" cy="10" r="1" fill="#fff"/><circle cx="10" cy="10" r="1" fill="#fff"/></svg>OUR SERVICES<span class="plus">+</span></li>
      <li><svg width="12" height="12"><path d="M6 0 7.8 4 12 4.4 8.8 7.2 9.7 11.5 6 9.3 2.3 11.5 3.2 7.2 0 4.4 4.2 4Z" fill="#fff"/></svg>GALLERY<span class="plus">+</span></li>
      <li><svg width="13" height="12"><rect x="1" y="2" width="9" height="9" fill="none" stroke="#fff" stroke-width="1.5"/><line x1="5" y1="8" x2="12" y2="1" stroke="#fff" stroke-width="2"/></svg>CAREERS<span class="plus">+</span></li>
      <li><svg width="14" height="11"><rect x="0" y="1" width="14" height="10" fill="#fff"/><path d="M0 1 7 6 14 1" fill="none" stroke="#8a0043"/></svg>&nbsp;CONTACT</li>
    </ul>
    <div class="side-title abs" style="top:276px">About Us</div>
    <p class="side-text abs">Lorem ipsum dolor sit amet, consectetur adipisic-<br>ing elit, sed do eiusmod tempor incididunt ut<br>labore et dolore magna aliqua. Ut enim ad minim<br>veniam, quis nostrud exercitation ullamco laboris<br>nisi ut aliquip ex ea commodo consequat....</p>
    <div class="side-title abs" style="top:435px">Recent Works</div>
    <div class="side-work abs" role="img" aria-label="Project workflow diagram sketched on glass"></div>
  </aside>

  <section class="hero abs" role="img" aria-label="Business team shaking hands across a meeting table">
    <div class="hero-title abs">Bluefern Business Services</div>
    <div class="hero-sub abs">Lorem ipsum dolor sit amet sed do euismod tempor incidunt magna aliqua..</div>
    <div class="dots abs"><i></i><i></i><i></i></div>
  </section>

  <div class="feature abs" style="left:423px">
    <h3><svg width="16" height="16"><rect width="16" height="16" fill="#333"/><rect x="7" y="6" width="2.5" height="7" fill="#fff"/><rect x="7" y="3" width="2.5" height="2" fill="#fff"/></svg>Packaged Applications</h3>
    <p>Lorem ipsum dolor sit amet conse adipsicing elit sed do incidunt magna aliqua...</p><span class="more">Read More</span>
  </div>
  <div class="feature abs" style="left:657px">
    <h3><svg width="18" height="14"><rect width="18" height="3" fill="#333"/><rect y="5" width="8" height="4" fill="#333"/><rect x="10" y="5" width="8" height="4" fill="#333"/><rect y="11" width="8" height="3" fill="#333"/><rect x="10" y="11" width="8" height="3" fill="#333"/></svg>Enterprise Application</h3>
    <p>Lorem ipsum dolor sit amet conse adipsicing elit sed do incidunt magna aliqua...</p><span class="more">Read More</span>
  </div>
  <div class="feature abs" style="left:892px">
    <h3><svg width="18" height="14"><path d="M0 4H4L9 0V14L4 10H0Z" fill="#333"/><path d="M12 3Q15 7 12 11M14 1Q18 7 14 13" fill="none" stroke="#333" stroke-width="1.5"/></svg>Digital Commerce</h3>
    <p>Lorem ipsum dolor sit amet conse adipsicing elit sed do incidunt magna aliqua...</p><span class="more">Read More</span>
  </div>

  <div class="sec-title abs" style="left:423px;top:645px">Recent Works</div>
  <div class="rule abs" style="left:410px;top:674px;width:680px"></div>
  <div class="work abs" style="left:423px"><div class="ph" role="img" aria-label="Job and internship fair crowd" style="background:linear-gradient(#2f3e5c,#6a6a6a)"></div><p>Lorem ipsum dolor sit amet conse adipsicing elit..</p></div>
  <div class="work abs" style="left:653px"><div class="ph" role="img" aria-label="Job fair event poster" style="background:linear-gradient(#ffffff,#f6efe8)"></div><p>Lorem ipsum dolor sit amet conse adipsicing elit..</p></div>
  <div class="work abs" style="left:884px"><div class="ph" role="img" aria-label="Job fair announcement with businessman" style="background:linear-gradient(90deg,#d8d8d8,#1a1a1a 55%)"></div><p>Lorem ipsum dolor sit amet conse adipsicing elit..</p></div>

  <div class="sec-title abs" style="left:423px;top:901px">Recent Posts</div>
  <div class="rule abs" style="left:423px;top:930px;width:309px"></div>
  <div class="post abs" style="top:951px">
    <div class="ico"><svg width="16" height="16"><path d="M2 14 3 10 11 2 14 5 6 13Z" fill="#fff"/></svg></div>
    <p>Lorem ipsum dolor sit amet conse adipsic-<br>ing elit, Sed do euismod magna aliqua...</p>
    <div class="meta"><span><svg width="10" height="10"><rect width="10" height="10" fill="none" stroke="#c06060" stroke-width="2"/></svg>Jan-15-2014</span><span><svg width="10" height="10"><circle cx="5" cy="3" r="3" fill="#c06060"/><rect x="1" y="6" width="8" height="4" fill="#c06060"/></svg>admin</span></div>
  </div>
  <div class="post abs" style="top:1028px">
    <div class="ico"><svg width="16" height="16"><path d="M2 14 3 10 11 2 14 5 6 13Z" fill="#fff"/></svg></div>
    <p>Lorem ipsum dolor sit amet conse adipsic-<br>ing elit, Sed do euismod magna aliqua...</p>
    <div class="meta"><span><svg width="10" height="10"><rect width="10" height="10" fill="none" stroke="#c06060" stroke-width="2"/></svg>Jan-15-2014</span><span><svg width="10" height="10"><circle cx="5" cy="3" r="3" fill="#c06060"/><rect x="1" y="6" width="8" height="4" fill="#c06060"/></svg>admin</span></div>
  </div>
  <div class="btn abs" style="left:423px;top:1108px;width:77px;height:33px;line-height:33px">View all</div>

  <div class="sec-title abs" style="left:781px;top:901px">Our Gallery</div>
  <div class="rule abs" style="left:781px;top:930px;width:309px"></div>
  <div class="thumb abs" style="left:782px;top:951px;background:linear-gradient(90deg,#ddd,#333)" role="img" aria-label="Businessman in suit"></div>
  <div class="thumb abs" style="left:886px;top:951px;background:linear-gradient(#2d4f6e,#5d7c96)" role="img" aria-label="Cloud services chart"></div>
  <div class="thumb abs" style="left:990px;top:951px;background:linear-gradient(135deg,#f2f4f6,#c8ced3)" role="img" aria-label="Workflow sketch"></div>
  <div class="thumb abs" style="left:782px;top:1023px;background:linear-gradient(#f0f0f0,#555)" role="img" aria-label="Team meeting"></div>
  <div class="thumb abs" style="left:886px;top:1023px;background:linear-gradient(135deg,#e6c9a8,#2a5fa8)" role="img" aria-label="Tablet shopping"></div>
  <div class="thumb abs" style="left:990px;top:1023px;background:linear-gradient(135deg,#eee,#9a8a80)" role="img" aria-label="Office colleagues"></div>
  <div class="btn abs" style="left:782px;top:1105px;width:127px;height:37px;line-height:37px">Upload Pictures</div>

  <footer class="site-footer abs">© Copyrights 2014 All rights Reserved</footer>
</div>
</body>
</html>
```